Scrum Master & Agile IT Coach Needing Business Website

Hello, my name is Joel Brandt
I am a project manger, scrum master, & agile coach. I work with IT development teams on major projects for Summit 300 companies . My project management business has a website and can be found here: www.tk-steadfast.example

I have launched a new company, ALL focused on IT Agile Coaching, I am looking to have a website created for my new company - the name of the new company is: Q's and V's - Agile IT Coaching and Training.
I have a logo and it is provided in the materials. I like to logo; I am open to different color pallets.

The website will have a total of 7 pages; I have content for 5 of the 7 pages prepared; the other 2 pages will say under construction.

Page 1 Who am I, What I do, My Experience
Demonstrated experience and progression from Scrum Master to
Program Manager to Coach

Page 2 Q's & V's - Agile Team Coaching
teams working major IT projects, multiple months/years

Page 3 Coaching @ the Team Level

Page 4 Coaching @ the Program Level ; LIMBr ART level

Pages 5 -6 Under Construction

Page 7 Presentations, Slide Decks, Reference Materials

Mentors Nook need to have this highlighted somewhere Monthly Blog
Updates

Industry/Entity Type

IT development

Coding

Coded - Design and coding required

Number of Pages Required

5+ page

Requirements
Must have
• the website must be bold - I want those who visit to remember coming to my coaching site
Nice to have
• nice to have will be a modern / futuristic website; I work with IT developers, I want a website they will like
Should not have
• should not be stiff - it should be professional but fun

```html
<!DOCTYPE html>
<html lang="en">
<head>
<meta charset="utf-8">
<title>Q's & V's — Joel Brandt, Agile IT Coaching</title>
<link rel="stylesheet" href="https://fonts.googleapis.com/css2?family=Michroma&family=Roboto:wght@400;500&display=swap">
<style>
:root{
  --navy:#123f8c;
  --navy-deep:#0e3378;
  --blue:#1670cc;
  --blue-bright:#1a7ae0;
  --ink:#333a44;
  --muted:#666c74;
  --soft:#f3f4f6;
  --white:#ffffff;
  --badge-navy:#24406e;
  --badge-orange:#ee8a2a;
  --badge-sky:#2a98dc;
  --badge-gold:#f1b52f;
}
*{margin:0;padding:0;box-sizing:border-box}
html,body{width:1200px;height:3571px;overflow:hidden}
body{position:relative;font-family:"Roboto",sans-serif;color:var(--ink);background:var(--white)}
.display{font-family:"Michroma",sans-serif;text-transform:uppercase}

/* header */
.site-header{position:absolute;left:0;top:0;width:1200px;height:132px;background:var(--navy);border-bottom:1px solid #3a63a8}
.brand{position:absolute;left:111px;top:38px;display:flex;align-items:center;gap:14px;color:var(--white)}
.brand-square{width:46px;height:46px;border:2px solid var(--white)}
.brand-name{font-family:"Michroma",sans-serif;font-size:30px;letter-spacing:1px;white-space:nowrap}
.main-nav a{position:absolute;top:57px;font-family:"Michroma",sans-serif;font-size:13px;color:var(--white);text-decoration:none;text-transform:uppercase;white-space:nowrap}
.main-nav .active{padding:8px 4px 8px 0;top:44px;border:1px solid var(--white);border-left:none}

/* hero */
.hero{position:absolute;left:0;top:132px;width:1200px;height:709px;background:linear-gradient(160deg,#5a544d 0%,#2f2d2b 45%,#1c1b1b 100%)}
.hero-title{position:absolute;left:0;width:1200px;top:508px;text-align:center;font-size:44px;color:var(--white)}
.hero-sub{position:absolute;left:0;width:1200px;top:582px;text-align:center;font-size:22px;color:var(--white)}
.hero-btn{position:absolute;left:507px;top:630px;width:186px;height:57px;border-radius:29px;background:var(--blue);color:var(--white);font-family:"Michroma",sans-serif;font-size:15px;display:flex;align-items:center;justify-content:center}
.hero-dots{position:absolute;top:809px;left:576px;display:flex;gap:7px}
.hero-dots span{width:11px;height:11px;border-radius:50%;background:var(--white)}
.hero-dots span.on{background:var(--blue-bright)}

/* about */
.portrait-ring{position:absolute;left:136px;top:930px;width:396px;height:396px;border-radius:50%;background:var(--navy)}
.portrait{position:absolute;left:144px;top:930px;width:384px;height:380px;border-radius:50%;background:radial-gradient(circle at 45% 45%,#8a6a4f,#5b5141 60%,#c9c4b2)}
.about-kicker{position:absolute;left:603px;top:940px;font-size:26px;color:var(--ink)}
.about-name{position:absolute;left:603px;top:978px;font-size:31px;color:var(--navy)}
.rule{position:absolute;height:3px;background:var(--navy)}
.about-text{position:absolute;left:600px;top:1048px;width:464px;font-family:Arial,sans-serif;font-size:13px;line-height:25.8px;color:var(--muted);text-align:justify}

/* designations */
.designations{position:absolute;left:0;top:1383px;width:1200px;height:541px;background:var(--soft)}
.section-title{position:absolute;left:0;width:1200px;text-align:center;font-size:27px;color:var(--navy)}
.badge{position:absolute;width:180px;height:180px;border-radius:50%;background:var(--white);box-shadow:0 2px 10px rgba(0,0,0,.12);display:flex;align-items:center;justify-content:center}
.badge-mark{width:124px;height:124px;border-radius:50%}

/* profile band */
.profile-band{position:absolute;left:0;top:1924px;width:1200px;height:113px;background:var(--blue)}
.profile-btn{position:absolute;top:30px;height:53px;border:2px solid var(--white);border-radius:3px;color:var(--white);font-family:"Michroma",sans-serif;font-size:12px;white-space:nowrap;display:flex;align-items:center;padding-left:20px}
.profile-btn .sep{position:absolute;right:42px;top:15px;width:1px;height:19px;background:var(--white)}
.profile-btn svg{position:absolute;right:14px;top:16px}

/* roles */
.role-icon{position:absolute;width:120px;height:120px;border:2px solid var(--blue);border-radius:50%;display:flex;align-items:center;justify-content:center}
.role-label{position:absolute;width:220px;text-align:center;font-size:17px;line-height:26px;color:var(--muted)}

/* experience */
.experience{position:absolute;left:0;top:2461px;width:1200px;height:756px;background:var(--soft)}
.crumbs{position:absolute;left:0;width:1200px;text-align:center;font-size:15px;line-height:33px;color:var(--muted)}
.crumbs a{color:var(--blue);text-decoration:underline}
.exp-heading{position:absolute;left:126px;top:2722px;font-size:24px;font-weight:500;color:var(--navy)}
.exp-list{position:absolute;left:126px;top:2804px;width:520px;list-style:none}
.exp-list li{position:relative;padding-left:28px;font-size:17px;line-height:21px;color:var(--ink);margin-bottom:24.5px}
.exp-list li::before{content:"»";position:absolute;left:0;top:-1px;color:var(--navy);font-size:19px}
.photo-frame{position:absolute;left:679px;top:2672px;width:376px;height:485px;border:3px solid var(--navy)}
.exp-photo{position:absolute;left:668px;top:2683px;width:377px;height:485px;background:linear-gradient(135deg,#2a3a44 0%,#3b3a38 45%,#6d4a2a 80%,#b38a3c 100%)}

/* footer */
.site-footer{position:absolute;left:0;top:3217px;width:1200px;height:354px;background:var(--navy-deep)}
.footer-brand{position:absolute;left:0;width:1200px;top:80px;display:flex;justify-content:center;align-items:center;gap:14px;color:var(--white)}
.footer-nav a{position:absolute;top:170px;transform:translateX(-50%);font-family:"Michroma",sans-serif;font-size:13px;color:var(--white);text-decoration:none;white-space:nowrap}
.social{position:absolute;top:216px;width:30px;height:30px;border:1.5px solid var(--white);border-radius:50%}
.copyright{position:absolute;left:0;width:1200px;top:275px;text-align:center;font-size:15px;color:var(--white)}
</style>
</head>
<body>

<header class="site-header">
  <div class="brand"><span class="brand-square"></span><span class="brand-name">Q's &amp; V's</span></div>
  <nav class="main-nav">
    <a class="active" style="left:468px">Home</a>
    <a style="left:560px">Who am I</a>
    <a style="left:686px">What I do</a>
    <a style="left:818px">My Experience</a>
    <a style="left:1003px">Contact</a>
  </nav>
</header>

<section class="hero" role="img" aria-label="Photo of a smiling team gathered around a laptop in an office"></section>
<h1 class="hero-title display">Joel Brandt</h1>
<p class="hero-sub display">Senior Scrum Master &amp; Team Agile Coach</p>
<a class="hero-btn">GET STARTED</a>
<div class="hero-dots"><span></span><span class="on"></span><span></span></div>

<section class="about">
  <div class="portrait-ring"></div>
  <div class="portrait" role="img" aria-label="Portrait photo of Joel Brandt"></div>
  <h2 class="about-kicker display">About</h2>
  <h2 class="about-name display">Joel Brandt</h2>
  <div class="rule" style="left:601px;top:1025px;width:48px"></div>
  <p class="about-text">Sed ut perspiciatis unde omnis iste natus error sit voluptatem accusantium doloremque laudantium, totam rem aperiam, eaque ipsa quae ab illo invento re veritatis et quasi architecto beatae vitae dicta sunt explicabo. Nemo enim ipsam voluptatem quia voluptas sit aspernatur aut odit aut fugit, sed quia consequuntur magni dolores eos qui ratione voluptatem sequi nesciunt. Neque porro quisquam est, qui dolorem ipsum quia dolor sit amet, cons ectetur, adipisci velit, sed quia non numquam eius modi tempora incidunt ut labore et dolore magnam aliquam quaerat voluptatem.</p>
</section>

<section class="designations">
  <h2 class="section-title display" style="top:60px">Coaching Designations</h2>
  <div class="rule" style="left:571px;top:108px;width:58px"></div>
  <div class="badge" style="left:216px;top:145px"><span class="badge-mark" style="background:var(--badge-navy)" role="img" aria-label="Certification badge"></span></div>
  <div class="badge" style="left:513px;top:145px"><span class="badge-mark" style="background:var(--badge-orange)" role="img" aria-label="Certification badge"></span></div>
  <div class="badge" style="left:810px;top:145px"><span class="badge-mark" style="background:var(--badge-sky)" role="img" aria-label="Certification badge"></span></div>
  <div class="badge" style="left:363px;top:314px"><span class="badge-mark" style="background:var(--badge-navy)" role="img" aria-label="Certification badge"></span></div>
  <div class="badge" style="left:660px;top:314px"><span class="badge-mark" style="background:var(--badge-gold)" role="img" aria-label="Certification badge"></span></div>
</section>

<section class="profile-band">
  <a class="profile-btn" style="left:67px;width:318px">AGILE GUILD PROFILE<span class="sep"></span><svg width="16" height="16" viewBox="0 0 16 16" fill="none" stroke="#fff" stroke-width="1.6"><rect x="1" y="6" width="7" height="4" rx="2" transform="rotate(45 4.5 8)"/><rect x="8" y="6" width="7" height="4" rx="2" transform="rotate(45 11.5 8)"/></svg></a>
  <a class="profile-btn" style="left:412px;width:318px">BADGEVAULT PROFILE<span class="sep"></span><svg width="16" height="16" viewBox="0 0 16 16" fill="none" stroke="#fff" stroke-width="1.6"><rect x="1" y="6" width="7" height="4" rx="2" transform="rotate(45 4.5 8)"/><rect x="8" y="6" width="7" height="4" rx="2" transform="rotate(45 11.5 8)"/></svg></a>
  <a class="profile-btn" style="left:755px;width:384px">LIMBr ADVANCED SCRUM MASTER<span class="sep"></span><svg width="16" height="16" viewBox="0 0 16 16" fill="none" stroke="#fff" stroke-width="1.6"><rect x="1" y="6" width="7" height="4" rx="2" transform="rotate(45 4.5 8)"/><rect x="8" y="6" width="7" height="4" rx="2" transform="rotate(45 11.5 8)"/></svg></a>
</section>

<section class="roles">
  <h2 class="section-title display" style="top:2098px">Roles I have held</h2>
  <div class="rule" style="left:571px;top:2148px;width:58px"></div>

  <div class="role-icon" style="left:174px;top:2205px"><svg width="62" height="56" viewBox="0 0 62 56" fill="none" stroke="#1670cc" stroke-width="2"><circle cx="31" cy="10" r="5"/><path d="M23 26v-5a8 8 0 0 1 16 0v5"/><rect x="38" y="2" width="14" height="12"/><circle cx="14" cy="36" r="5"/><circle cx="31" cy="36" r="5"/><circle cx="48" cy="36" r="5"/><path d="M5 52a9 9 0 0 1 18 0M22 52a9 9 0 0 1 18 0M39 52a9 9 0 0 1 18 0"/></svg></div>
  <p class="role-label" style="left:124px;top:2339px">Sr. Scrum Master</p>

  <div class="role-icon" style="left:425px;top:2205px"><svg width="50" height="58" viewBox="0 0 50 58" fill="none" stroke="#1670cc" stroke-width="2"><path d="M25 3 L46 11 V28 C46 42 36 51 25 55 C14 51 4 42 4 28 V11 Z"/><path d="M15 29 l7 7 13 -14"/></svg></div>
  <p class="role-label" style="left:375px;top:2339px">Advanced LIMBr<br>Scrum Master</p>

  <div class="role-icon" style="left:675px;top:2205px"><svg width="64" height="58" viewBox="0 0 64 58" fill="none" stroke="#1670cc" stroke-width="2"><circle cx="16" cy="29" r="6"/><circle cx="16" cy="29" r="11" stroke-dasharray="4 3"/><rect x="40" y="4" width="12" height="10"/><rect x="40" y="24" width="12" height="10"/><rect x="40" y="44" width="12" height="10"/><path d="M27 29h7M34 9v40M34 9h6M34 29h6M34 49h6"/></svg></div>
  <p class="role-label" style="left:625px;top:2339px">Hybrid Scrum Master<br>Project Manager</p>

  <div class="role-icon" style="left:925px;top:2205px"><svg width="60" height="58" viewBox="0 0 60 58" fill="none" stroke="#1670cc" stroke-width="2"><rect x="20" y="4" width="36" height="30"/><path d="M28 26l8-8 5 5 8-10"/><circle cx="10" cy="16" r="5"/><path d="M4 54V28h12v26M10 54V40M16 30l8-6"/></svg></div>
  <p class="role-label" style="left:875px;top:2339px">Business Finance<br>Transformation Program<br>Manager</p>
</section>

<section class="experience">
  <h2 class="section-title display" style="top:40px">What is my Experience</h2>
  <div class="rule" style="left:571px;top:91px;width:58px"></div>
  <p class="crumbs" style="top:111px"><a>As a LIMBr Adv Scrum Master, I</a>&nbsp;&nbsp; / &nbsp;&nbsp;As a Hybrid Scrum Master / Project Manager, I<br>Business Transformation Program Manager</p>
</section>
<h3 class="exp-heading">As a LIMBr Adv Scrum Master, I</h3>
<div class="rule" style="left:126px;top:2764px;width:44px"></div>
<ul class="exp-list">
  <li>stand up teams</li>
  <li>run development efforts concurrently leading multiple teams</li>
  <li>run LIMBr ceremonies</li>
  <li>Scrum of Scrums facilitator</li>
  <li>PI Planning team facilitator (multiple teams on ART)</li>
  <li>Teach and coach to advanced development team strategies</li>
  <li>Lead program level communications and business status updates on behalf of the team</li>
</ul>
<div class="photo-frame"></div>
<div class="exp-photo" role="img" aria-label="Photo of a coach with a headset writing on a glass board covered with sticky notes"></div>

<footer class="site-footer">
  <div class="footer-brand"><span class="brand-square"></span><span class="brand-name">Q's &amp; V's</span></div>
  <nav class="footer-nav">
    <a style="left:316px">HOME</a>
    <a style="left:425px">WHO AM I</a>
    <a style="left:553px">WHAT I DO</a>
    <a style="left:712px">MY EXPERIENCE</a>
    <a style="left:867px">CONTACT</a>
  </nav>
  <span class="social" style="left:509px" aria-label="Social link"></span>
  <span class="social" style="left:547px" aria-label="Social link"></span>
  <span class="social" style="left:585px" aria-label="Social link"></span>
  <span class="social" style="left:623px" aria-label="Social link"></span>
  <span class="social" style="left:661px" aria-label="Social link"></span>
  <p class="copyright">© Copyright 2022 Joel Brandt.All Rights Reserved</p>
</footer>

</body>
</html>
```